FinTech company looking to revamp and expand client-facing interface for our financial models

Pellworth Engines currently has a very simple website that allows clients to interact with our financial models. We are looking to completely redesign the current site and add several extra pages to provide extra functionality. We want the design to have a modern, slick feel, that will work on both a desktop or a tablet. It should be straightforward for clients to move between different pages at any time, and clear from the layout how to interact with the more advanced features. We have included screenshots of existing pages in the attached design brief, as well as sketches of the functionality required by the new pages, but can't provide a direct link to the current site.
Target Market(s)
Professional investors that will be paying to access the interface
Industry/Entity Type
Finance
Number of Pages Required
4 page
Colors
Designer to choose colors to be used in the design.
Look and feel
Each slider illustrates characteristics of the customer's brand and the style your logo design should communicate.

```html
<!DOCTYPE html>
<html lang="en">
<head>
<meta charset="utf-8">
<title>Pellworth Engines – Portfolio</title>
<link href="https://fonts.googleapis.com/css2?family=Montserrat:wght@500;600;700&family=Roboto+Condensed:wght@400;500&display=swap" rel="stylesheet">
<style>
:root{
  --frame:#e6e6e6;
  --white:#ffffff;
  --navy:#0b3a78;
  --teal:#0f6b66;
  --ink:#1b1b1b;
  --line:#dcdcdc;
  --dim-bg:#3c3c3c;
  --dim-panel:#414141;
  --dim-row:#3f3f3f;
  --dim-head:#272727;
  --dim-teal:#2c4744;
  --dim-text:#575757;
  --dim-navy:#202d45;
  --dim-green:#2f4a2c;
  --dim-red:#6b3f3f;
  --soft:#f0f0f0;
  --track:#c9c9c9;
}
*{box-sizing:border-box;margin:0;padding:0}
html,body{width:1169px;height:1200px;overflow:hidden;background:var(--frame)}
.stage{position:absolute;left:0;top:0;width:1300px;height:1335px;transform:scale(0.8985);transform-origin:0 0;font-family:"Montserrat",sans-serif;color:var(--ink)}
.abs{position:absolute}
/* navigation */
.topnav{left:15px;top:15px;width:1270px;height:60px;background:var(--white);display:flex}
.topnav .cell{height:60px;border-right:1px solid var(--line);display:flex;align-items:center;justify-content:center;font-weight:700;font-size:14px;gap:8px;letter-spacing:.2px}
.topnav .brand{width:180px;font-size:18px}
.topnav .range{width:90px}
.topnav .gap{width:135px}
.topnav .active{background:var(--navy);color:var(--white);border-right:none}
.topnav svg{width:24px;height:24px}
/* dimmed page */
.page{left:15px;top:75px;width:1270px;height:1245px;background:var(--dim-bg)}
.panel{background:var(--dim-panel)}
.panel-head{background:var(--dim-head);color:var(--dim-text);font-weight:600;font-size:17px;display:flex;align-items:center;justify-content:center}
.col-head{background:var(--dim-teal);color:#4f6a67;font-weight:600;font-size:16px}
.member-row{left:70px;width:560px;height:69px;display:flex;align-items:center;font-family:"Roboto Condensed",sans-serif;font-size:17px;color:var(--dim-text);padding-left:50px;gap:20px}
.member-row:nth-of-type(odd){background:var(--dim-row)}
.member-row svg{width:26px;height:26px}
.dim-btn{height:40px;border-radius:3px;display:flex;align-items:center;gap:8px;padding-left:16px;font-size:13px;font-weight:700;color:#4d5566}
.sens-row{left:945px;width:250px;height:36px;background:#454545}
.sens-val{font-family:"Roboto Condensed",sans-serif;font-size:17px;color:var(--dim-text)}
.tab{top:865px;height:35px;display:flex;align-items:center;justify-content:center;font-size:13px;font-weight:600;color:#4e4e4e}
/* modal */
.modal{left:370px;top:150px;width:560px;height:670px;background:var(--white);overflow:hidden}
.modal-head{height:50px;background:var(--navy);color:var(--white);font-weight:600;font-size:17px;display:flex;align-items:center;justify-content:center}
.field-label{left:28px;font-weight:600;font-size:16px}
.field{left:192px;width:228px;height:30px;border:1px solid #bdbdbd;border-radius:3px;font-family:"Roboto Condensed",sans-serif;font-size:16px;display:flex;align-items:center;padding-left:12px}
.btn-search{left:430px;width:104px;height:30px;background:var(--teal);color:var(--white);font-weight:600;font-size:15px;border-radius:2px;display:flex;align-items:center;justify-content:center;box-shadow:0 0 0 1px #9fbcba}
.result{left:0;width:520px;height:69px;display:flex;align-items:center;padding-left:27px;font-family:"Roboto Condensed",sans-serif;font-size:18px;font-weight:500}
.result.selected{background:var(--teal);color:var(--white)}
.result.alt{background:var(--soft)}
.scroll-track{left:520px;top:250px;width:40px;height:350px;background:var(--track)}
.scroll-lane{left:532px;top:275px;width:16px;height:298px;background:var(--white);border-radius:8px}
.scroll-thumb{left:530px;top:275px;width:20px;height:74px;background:#9a9a9a;border-radius:8px}
.modal-foot{left:0;top:600px;width:560px;height:70px;background:var(--soft)}
.btn-add{left:196px;top:615px;width:168px;height:40px;background:var(--navy);color:var(--white);border-radius:3px;display:flex;align-items:center;justify-content:center;gap:8px;font-weight:700;font-size:14px}
</style>
</head>
<body>
<div class="stage">
  <nav class="abs topnav">
    <div class="cell brand">KESTREL</div>
    <div class="cell range">250D</div>
    <div class="cell range">83D</div>
    <div class="cell range">42D</div>
    <div class="cell gap"></div>
    <div class="cell" style="width:140px">
      <svg viewBox="0 0 24 24"><path d="M2 12 12 3l10 9h-3v9h-5v-6h-4v6H5v-9z" fill="#111"/></svg>MODELS</div>
    <div class="cell" style="width:178px">
      <svg viewBox="0 0 24 24" fill="none" stroke="#111" stroke-width="1.6"><circle cx="12" cy="12" r="3"/><circle cx="12" cy="12" r="7" stroke-dasharray="2 2"/><circle cx="12" cy="12" r="10.5" stroke-dasharray="1.5 2.5"/></svg>SENSITIVITIES</div>
    <div class="cell active" style="width:162px">
      <svg viewBox="0 0 24 24" fill="none" stroke="#fff" stroke-width="1.8"><circle cx="6.5" cy="6.5" r="4.3"/><circle cx="17.5" cy="6.5" r="4.3"/><circle cx="6.5" cy="17.5" r="4.3"/><circle cx="17.5" cy="17.5" r="4.3"/></svg>PORTFOLIO</div>
    <div class="cell" style="width:150px">
      <svg viewBox="0 0 24 24" fill="none" stroke="#111" stroke-width="1.8"><rect x="2" y="4" width="20" height="16"/><path d="M5 16l4-5 3 3 4-6 3 4"/></svg>BACKTEST</div>
  </nav>

  <main class="abs page"></main>

  <!-- current members (behind dialog) -->
  <section class="abs panel" style="left:70px;top:115px;width:560px;height:515px">
    <div class="panel-head" style="height:50px">Current Members</div>
    <div class="col-head" style="height:50px;display:flex;align-items:center;padding-left:61px;width:260px;border-right:2px solid #3a3a3a">Members Name</div>
  </section>
  <div>
    <div class="abs member-row" style="top:218px"><svg viewBox="0 0 26 26" fill="none" stroke="var(--dim-red)" stroke-width="1.5"><circle cx="13" cy="13" r="11"/><path d="M13 7v12M7 13h12"/></svg>Member 1</div>
    <div class="abs member-row" style="top:287px"><svg viewBox="0 0 26 26" fill="none" stroke="var(--dim-red)" stroke-width="1.5"><circle cx="13" cy="13" r="11"/><path d="M13 7v12M7 13h12"/></svg>Member 2</div>
    <div class="abs member-row" style="top:356px"><svg viewBox="0 0 26 26" fill="none" stroke="var(--dim-red)" stroke-width="1.5"><circle cx="13" cy="13" r="11"/><path d="M13 7v12M7 13h12"/></svg>Member 3</div>
    <div class="abs member-row" style="top:425px"><svg viewBox="0 0 26 26" fill="none" stroke="var(--dim-red)" stroke-width="1.5"><circle cx="13" cy="13" r="11"/><path d="M13 7v12M7 13h12"/></svg>Member 4</div>
    <div class="abs member-row" style="top:494px"><svg viewBox="0 0 26 26" fill="none" stroke="var(--dim-red)" stroke-width="1.5"><circle cx="13" cy="13" r="11"/><path d="M13 7v12M7 13h12"/></svg>Member 5</div>
    <div class="abs member-row" style="top:563px"><svg viewBox="0 0 26 26" fill="none" stroke="var(--dim-red)" stroke-width="1.5"><circle cx="13" cy="13" r="11"/><path d="M13 7v12M7 13h12"/></svg>Member 6</div>
  </div>
  <div class="abs dim-btn" style="left:70px;top:655px;width:168px;background:var(--dim-navy)">
    <svg width="20" height="20" viewBox="0 0 20 20" fill="none" stroke="#4d5566" stroke-width="1.5"><circle cx="10" cy="10" r="9"/><path d="M10 5v10M5 10h10"/></svg>ADD A MEMBER</div>
  <div class="abs dim-btn" style="left:249px;top:655px;width:140px;background:var(--dim-green);color:#4e6a4a">
    <svg width="22" height="20" viewBox="0 0 22 20" fill="none" stroke="#4e8a46" stroke-width="3"><path d="M2 10l6 6L20 3"/></svg>SAVE PORT</div>

  <!-- sensitivities (behind dialog) -->
  <section class="abs panel" style="left:670px;top:115px;width:560px;height:345px">
    <div class="panel-head" style="height:70px;background:var(--dim-teal);color:#47625e">Sensitivities</div>
  </section>
  <div class="abs sens-row" style="top:201px"></div>
  <div class="abs sens-row" style="top:271px"></div>
  <div class="abs sens-row" style="top:342px"></div>
  <div class="abs sens-row" style="top:412px"></div>
  <div class="abs" style="left:1044px;top:195px;width:2px;height:260px;background:#333"></div>
  <div class="abs" style="left:1046px;top:202px;width:66px;height:35px;background:#2c4e26"></div>
  <div class="abs" style="left:1046px;top:272px;width:52px;height:35px;background:#2c4e26"></div>
  <div class="abs" style="left:1005px;top:345px;width:39px;height:29px;background:#5a2323"></div>
  <div class="abs" style="left:1026px;top:416px;width:18px;height:28px;background:#5a2323"></div>
  <div class="abs sens-val" style="left:1125px;top:207px">0.9</div>
  <div class="abs sens-val" style="left:1111px;top:278px">0.7</div>
  <div class="abs sens-val" style="left:968px;top:350px">-0.6</div>
  <div class="abs sens-val" style="left:989px;top:420px">-0.3</div>

  <!-- chart (behind dialog) -->
  <section class="abs panel" style="left:65px;top:810px;width:1165px;height:430px"></section>
  <div class="abs tab" style="left:125px;width:155px;background:var(--dim-navy);color:#4a5468">CHART</div>
  <div class="abs tab" style="left:285px;width:90px">#1</div>
  <div class="abs tab" style="left:380px;width:90px">#2</div>
  <div class="abs tab" style="left:475px;width:90px">#3</div>
  <div class="abs tab" style="left:570px;width:90px;top:855px;height:45px;background:#2b2b2b">#4</div>
  <svg class="abs" style="left:65px;top:810px" width="1165" height="430" viewBox="65 810 1165 430" role="img" aria-label="Scatter chart of member scores over time">
    <g font-family="Georgia,serif" font-size="11" fill="#555">
      <text x="131" y="967">100</text><text x="137" y="1004">80</text><text x="137" y="1041">60</text>
      <text x="137" y="1079">40</text><text x="137" y="1116">20</text><text x="144" y="1153">0</text>
      <text x="160" y="1175">Jul 2018</text><text x="300" y="1175">Sep 2018</text><text x="440" y="1175">Nov 2018</text>
      <text x="582" y="1175">Jan 2019</text><text x="716" y="1175">Mar 2019</text><text x="856" y="1175">May 2019</text>
      <text x="1000" y="1175">Jul 2019</text><text x="1132" y="965">Names</text>
    </g>
    <line x1="152" y1="1149" x2="1075" y2="1149" stroke="#555"/>
    <g stroke-linecap="round" stroke-dasharray="0 6" stroke-width="6" fill="none">
      <line x1="202" y1="963" x2="285" y2="963" stroke="#5c5c36"/>
      <line x1="540" y1="965" x2="600" y2="965" stroke="#5c5c36"/>
      <line x1="590" y1="963" x2="1026" y2="963" stroke="#2c3c5c"/>
    </g>
    <g fill="#5c5c36">
      <circle cx="290" cy="970" r="3"/><circle cx="300" cy="968" r="3"/><circle cx="315" cy="972" r="3"/><circle cx="332" cy="975" r="3"/>
      <circle cx="338" cy="1030" r="3"/><circle cx="350" cy="1042" r="3"/><circle cx="355" cy="1065" r="3"/><circle cx="362" cy="1080" r="3"/>
      <circle cx="372" cy="1060" r="3"/><circle cx="380" cy="1025" r="3"/><circle cx="388" cy="1003" r="3"/><circle cx="395" cy="992" r="3"/>
      <circle cx="402" cy="968" r="3"/><circle cx="410" cy="1025" r="3"/><circle cx="420" cy="1060" r="3"/><circle cx="428" cy="1048" r="3"/>
      <circle cx="440" cy="1115" r="3"/><circle cx="450" cy="1108" r="3"/><circle cx="458" cy="1098" r="3"/><circle cx="470" cy="1140" r="3"/>
      <circle cx="486" cy="1130" r="3"/><circle cx="500" cy="1128" r="3"/><circle cx="578" cy="1138" r="3"/><circle cx="594" cy="1135" r="3"/>
      <circle cx="612" cy="1128" r="3"/><circle cx="632" cy="1135" r="3"/><circle cx="645" cy="1110" r="3"/><circle cx="655" cy="1095" r="3"/>
      <circle cx="660" cy="1060" r="3"/><circle cx="668" cy="1025" r="3"/><circle cx="672" cy="985" r="3"/><circle cx="690" cy="982" r="3"/>
      <circle cx="705" cy="995" r="3"/><circle cx="712" cy="1020" r="3"/><circle cx="722" cy="1062" r="3"/><circle cx="738" cy="975" r="3"/>
      <circle cx="752" cy="978" r="3"/><circle cx="696" cy="1108" r="3"/><circle cx="700" cy="1115" r="3"/><circle cx="255" cy="963" r="3"/>
    </g>
    <g fill="#2c3c5c">
      <circle cx="205" cy="970" r="3"/><circle cx="218" cy="972" r="3"/><circle cx="203" cy="1028" r="3"/><circle cx="222" cy="1045" r="3"/>
      <circle cx="230" cy="1078" r="3"/><circle cx="240" cy="1090" r="3"/><circle cx="250" cy="1098" r="3"/><circle cx="256" cy="1040" r="3"/>
      <circle cx="262" cy="1068" r="3"/><circle cx="270" cy="1050" r="3"/><circle cx="278" cy="1100" r="3"/><circle cx="292" cy="1080" r="3"/>
      <circle cx="300" cy="1095" r="3"/><circle cx="312" cy="1105" r="3"/><circle cx="322" cy="1098" r="3"/><circle cx="335" cy="1125" r="3"/>
      <circle cx="348" cy="1130" r="3"/><circle cx="362" cy="1125" r="3"/><circle cx="378" cy="1105" r="3"/><circle cx="392" cy="1095" r="3"/>
      <circle cx="405" cy="1110" r="3"/><circle cx="418" cy="1092" r="3"/><circle cx="432" cy="1145" r="3"/><circle cx="446" cy="1140" r="3"/>
      <circle cx="463" cy="1020" r="3"/><circle cx="470" cy="990" r="3"/><circle cx="480" cy="975" r="3"/><circle cx="490" cy="1000" r="3"/>
      <circle cx="505" cy="1100" r="3"/><circle cx="515" cy="1085" r="3"/><circle cx="525" cy="1110" r="3"/><circle cx="532" cy="1048" r="3"/>
      <circle cx="540" cy="1070" r="3"/><circle cx="546" cy="985" r="3"/><circle cx="560" cy="975" r="3"/><circle cx="570" cy="972" r="3"/>
      <circle cx="578" cy="965" r="3"/><circle cx="242" cy="1080" r="3"/>
    </g>
    <g fill="#2c4a28"><circle cx="1000" cy="1147" r="3"/><circle cx="1008" cy="1147" r="3"/></g>
    <g>
      <circle cx="1114" cy="962" r="3" fill="#4a4a3a"/><circle cx="1114" cy="980" r="3" fill="#4a4a3a"/><circle cx="1114" cy="999" r="3" fill="#2c4a28"/>
      <circle cx="1114" cy="1017" r="3" fill="#484848"/><circle cx="1114" cy="1036" r="3" fill="#484848"/><circle cx="1114" cy="1054" r="3" fill="#4a4a3a"/>
      <circle cx="1114" cy="1073" r="3" fill="#484848"/><circle cx="1114" cy="1092" r="3" fill="#4a4a3a"/><circle cx="1114" cy="1110" r="3" fill="#4a4a3a"/>
      <circle cx="1114" cy="1129" r="3" fill="#3a4a4a"/><circle cx="1114" cy="1147" r="3" fill="#2c3c5c"/>
    </g>
    <path d="M627 880v14l-3-3-3 2 5 8 4 4h9l3-6v-8l-3-1-2 1-2-1-2 1v-11z" fill="#2b2b2b" stroke="#555" stroke-width="1.3"/>
  </svg>

  <!-- dialog -->
  <section class="abs modal" role="dialog" aria-label="Add a Member">
    <header class="modal-head">Add a Member</header>
    <div class="abs field-label" style="top:65px">Search Database</div>
    <div class="abs field" style="top:60px">Name</div>
    <div class="abs btn-search" style="top:60px">Search</div>
    <div class="abs" style="left:0;top:100px;width:560px;height:1px;background:var(--line)"></div>
    <div class="abs field-label" style="top:115px">Filter by Sector</div>
    <div class="abs field" style="top:110px">Select sector
      <svg style="position:absolute;right:10px;top:11px" width="16" height="9" viewBox="0 0 16 9"><path d="M0 0h16L8 9z" fill="#333"/></svg></div>
    <div class="abs btn-search" style="top:110px">Search</div>
    <div class="abs" style="left:0;top:150px;width:560px;height:1px;background:var(--line)"></div>
    <div class="abs field-label" style="top:207px;left:27px;font-weight:500;font-size:17px">Search Results</div>
    <div class="abs" style="left:430px;top:207px;width:20px;height:20px;border:1px solid #bbb;border-radius:3px"></div>
    <div class="abs" style="left:457px;top:209px;font-size:13px;font-weight:700">Select All</div>
    <div class="abs" style="left:0;top:250px;width:520px;height:1px;background:#eee"></div>
    <div class="abs result" style="top:250px">Member 1</div>
    <div class="abs result selected" style="top:320px">Member 2</div>
    <div class="abs result" style="top:389px">Member 3</div>
    <div class="abs result alt" style="top:458px">Member 4</div>
    <div class="abs result" style="top:527px">Member 5</div>
    <div class="abs scroll-track"></div>
    <div class="abs scroll-lane"></div>
    <div class="abs scroll-thumb"></div>
    <svg class="abs" style="left:366px;top:358px" width="28" height="38" viewBox="0 0 28 38">
      <path d="M8 2a2.5 2.5 0 0 1 5 0v13l1-1a2.5 2.5 0 0 1 4 1a2.5 2.5 0 0 1 4 1a2.5 2.5 0 0 1 4 1v10c0 4-3 8-6 8h-8c-3 0-5-3-7-6l-4-7a2.5 2.5 0 0 1 4-3l3 3z" fill="#fff" stroke="#000" stroke-width="1.4" stroke-linejoin="round"/>
      <path d="M13 20v7M17 20v7M21 21v6" stroke="#000" stroke-width="1.2"/>
    </svg>
    <div class="abs modal-foot"></div>
    <div class="abs btn-add">
      <svg width="22" height="22" viewBox="0 0 22 22" fill="none" stroke="#fff" stroke-width="1.6"><circle cx="11" cy="11" r="9.5"/><path d="M11 6v10M6 11h10"/></svg>ADD MEMBER</div>
  </section>
</div>
</body>
</html>
```